Lifecoach needs website design based on a standard Wordpress theme

I need a website for my new lifecoaching business that can be easily implemented in Wordpress, it needs to be compatible with a standard Wordpress theme. So I can place the pictures, texts etc. in a standard theme of Wordpress.

I want the design to be a very good feeling and playfull one, based on my logo.

Target Market(s)

I will coach people to reach their goals and dreams in life.

Industry/Entity Type

Business

Requirements
Must have
• Can be easy implemented in Wordpress.
Nice to have
• Photo's of nature are nice.

```html
<!DOCTYPE html>
<html lang="en">
<head>
<meta charset="utf-8">
<title>Maren Holt Lifecoach</title>
<link href="https://fonts.googleapis.com/css2?family=Open+Sans:wght@400;600&display=swap" rel="stylesheet">
<style>
:root{
  --blue:#1aa3e8;
  --blue-dark:#0d8fd3;
  --ink:#1e1e1e;
  --text:#444;
  --muted:#f6f6f6;
  --line:#e4e4e4;
  --footer:#4a4a4a;
  --nav-home:#4a4a4a;
  --font:'Open Sans',Arial,sans-serif;
}
*{margin:0;padding:0;box-sizing:border-box}
html,body{width:752px;height:1200px;overflow:hidden;background:#fff;font-family:var(--font);color:var(--ink)}
.page{position:relative;width:752px;height:1200px}
.abs{position:absolute}
.brand{left:113px;top:16px;display:flex;align-items:center;gap:8px}
.brand-dot{width:44px;height:44px;border-radius:50%;border:3px solid var(--blue-dark)}
.brand-name{font-size:15px;font-weight:400;color:var(--blue-dark);line-height:1.25;letter-spacing:.5px}
.call{left:540px;top:24px;display:flex;gap:10px;align-items:center}
.call-text{font-size:10px;line-height:20px;color:var(--ink)}
.nav{left:0;top:79px;width:752px;height:32px;background:linear-gradient(#22b0f0,#0e96dc);border-bottom:2px solid #555}
.nav-home{position:absolute;left:113px;top:0;width:51px;height:30px;background:var(--nav-home);display:flex;align-items:center;justify-content:center}
.nav-item{position:absolute;top:0;height:30px;line-height:30px;font-size:7.5px;font-weight:600;color:#fff}
.nav-sep{position:absolute;top:0;width:1px;height:30px;background:rgba(255,255,255,.25)}
.hero{left:0;top:111px;width:752px;height:308px;background:linear-gradient(160deg,#6a9fd8 0%,#a9c8e4 55%,#b9cf92 100%)}
.hero-caption{left:343px;top:215px;width:242px;height:83px;background:rgba(110,115,120,.85);color:#fff;font-size:27px;line-height:35px;padding:6px 0 0 16px;white-space:nowrap}
.hero-arrow{width:22px;height:22px;border-radius:50%;background:rgba(255,255,255,.8);display:flex;align-items:center;justify-content:center}
.hero-line{left:0;top:419px;width:752px;height:2px;background:var(--blue)}
.features{left:0;top:421px;width:752px;height:200px;background:var(--muted);border-bottom:1px solid var(--line)}
.feature{position:absolute;top:27px;width:150px;text-align:center}
.feature-icon{width:78px;height:78px;border-radius:50%;background:#fff;border:1px solid #ddd;margin:0 auto;display:flex;align-items:center;justify-content:center}
.feature h3{font-size:10px;font-weight:600;margin-top:15px}
.feature p{font-size:6.4px;line-height:12px;color:var(--text);margin-top:9px}
.card{position:absolute;top:648px;width:165px}
.card-photo{width:165px;height:103px;border:3px solid #fff;outline:1px solid #e2e2e2}
.card h2{font-size:12.4px;font-weight:400;margin-top:18px;white-space:nowrap;letter-spacing:-.1px}
.card p{font-size:6.6px;line-height:11.8px;color:var(--text);margin-top:10px;text-align:justify}
.btn{display:inline-block;margin-top:11px;width:60px;height:23px;line-height:23px;text-align:center;background:var(--blue);color:#fff;font-size:7px;border-radius:2px}
.news-title{left:113px;top:907px;font-size:13.5px;font-weight:400}
.news-title span{color:var(--blue)}
.news-rule{left:113px;top:935px;width:526px;height:1px;background:var(--line)}
.news{position:absolute;top:951px;width:257px;height:117px;border:1px solid var(--line);background:#fafafa}
.news-photo{position:absolute;left:12px;top:11px;width:87px;height:80px;border:3px solid #fff;outline:1px solid #ddd}
.news-body{position:absolute;left:108px;top:9px;width:138px}
.news-body h4{font-size:9.6px;font-weight:400;white-space:nowrap}
.news-date{font-size:6px;margin-top:8px}
.news-body p{font-size:6.2px;line-height:11.8px;color:var(--text);margin-top:6px;text-align:justify}
.news-more{font-size:6px;color:var(--blue);text-align:right;margin-top:2px}
.subscribe{left:0;top:1091px;width:752px;height:52px;background:linear-gradient(#22aef0,#1593d8)}
.subscribe-label{position:absolute;left:145px;top:19px;font-size:10px;color:#111;letter-spacing:.2px;white-space:nowrap}
.subscribe-input{position:absolute;left:313px;top:14px;width:232px;height:25px;background:#fff;border:1px solid #cfe8f5;font-size:6.5px;padding:0 10px;line-height:24px;color:#333}
.subscribe-btn{position:absolute;left:564px;top:13px;width:75px;height:26px;background:#2b2b2b;color:#fff;font-size:10px;text-align:center;line-height:26px}
.footer{left:0;top:1143px;width:752px;height:57px;background:var(--footer)}
.footer-links{position:absolute;left:115px;top:13px;font-size:6.5px;color:#ddd}
.footer-copy{position:absolute;left:115px;top:32px;font-size:6.5px;color:#ddd}
.social{position:absolute;left:569px;top:21px;display:flex;gap:6px}
.social span{width:13px;height:13px;border-radius:50%;background:#fff}
</style>
</head>
<body>
<div class="page">
  <div class="abs brand"><span class="brand-dot"></span><span class="brand-name">Maren Holt<br>Lifecoach</span></div>
  <div class="abs call">
    <svg width="16" height="30" viewBox="0 0 16 30"><rect x="1" y="1" width="14" height="28" rx="2" fill="none" stroke="#111" stroke-width="2"/><rect x="3" y="5" width="10" height="17" fill="#111"/><circle cx="8" cy="25" r="1.4" fill="#111"/></svg>
    <div class="call-text">Call For Info<br>+1-555-014-2290</div>
  </div>

  <nav class="abs nav">
    <div class="nav-home"><svg width="15" height="13" viewBox="0 0 15 13"><path d="M7.5 0L0 6.5h2V13h4V9h3v4h4V6.5h2z" fill="#fff"/></svg></div>
    <span class="nav-item" style="left:185px">About Us</span><span class="nav-sep" style="left:232px"></span>
    <span class="nav-item" style="left:255px">Life Coaching</span><span class="nav-sep" style="left:320px"></span>
    <span class="nav-item" style="left:338px">Professional Empowerment</span><span class="nav-sep" style="left:459px"></span>
    <span class="nav-item" style="left:474px">Our Courses</span><span class="nav-sep" style="left:538px"></span>
    <span class="nav-item" style="left:552px">Contact Us</span><span class="nav-sep" style="left:606px"></span>
  </nav>

  <div class="abs hero" role="img" aria-label="Slider photo: a man with raised arms standing in a meadow under a cloudy sky"></div>
  <div class="abs hero-caption">Life Coaching for<br>Personal</div>
  <div class="abs hero-arrow" style="left:30px;top:247px"><svg width="8" height="8" viewBox="0 0 8 8"><path d="M5 1L2 4l3 3" fill="none" stroke="#555" stroke-width="1.5"/></svg></div>
  <div class="abs hero-arrow" style="left:697px;top:247px"><svg width="8" height="8" viewBox="0 0 8 8"><path d="M3 1l3 3-3 3" fill="none" stroke="#555" stroke-width="1.5"/></svg></div>
  <div class="abs hero-line"></div>

  <section class="abs features">
    <div class="feature" style="left:109px">
      <div class="feature-icon"><svg width="46" height="44" viewBox="0 0 46 44"><circle cx="23" cy="8" r="7" fill="#111"/><path d="M10 22q13-8 26 0v8H10z" fill="#111"/><path d="M2 26l21 6 21-6v14l-21 4-21-4z" fill="#111"/><path d="M23 33v10" stroke="#fff" stroke-width="1.5"/></svg></div>
      <h3>Best Coaches</h3>
      <p>Praesent vestibulum molestie lacus. Aenean nonummy hendrerit mauris. Phasellus porta. Fusce suscipit varius.</p>
    </div>
    <div class="feature" style="left:303px">
      <div class="feature-icon"><svg width="42" height="32" viewBox="0 0 42 32"><rect x="1" y="1" width="40" height="24" fill="#111"/><rect x="5" y="5" width="32" height="16" fill="#fff"/><rect x="14" y="7" width="10" height="11" fill="none" stroke="#111" stroke-width="2"/><rect x="20" y="11" width="7" height="9" fill="#111"/><rect x="17" y="25" width="8" height="4" fill="#111"/><rect x="11" y="29" width="20" height="2" fill="#111"/></svg></div>
      <h3>What is Online Coaching?</h3>
      <p>Praesent vestibulum molestie lacus. Aenean nonummy hendrerit mauris. Phasellus porta. Fusce suscipit varius.</p>
    </div>
    <div class="feature" style="left:497px">
      <div class="feature-icon"><svg width="46" height="40" viewBox="0 0 46 40"><ellipse cx="23" cy="11" rx="11" ry="9" fill="#111"/><ellipse cx="11" cy="27" rx="11" ry="8" fill="#111"/><ellipse cx="35" cy="27" rx="11" ry="8" fill="#111"/><path d="M21 19l2 5 2-5zM8 34l2 6 4-6zM32 34l4 6 2-6z" fill="#111"/></svg></div>
      <h3>How We Can Help You?</h3>
      <p>Praesent vestibulum molestie lacus. Aenean nonummy hendrerit mauris. Phasellus porta. Fusce suscipit varius.</p>
    </div>
  </section>

  <article class="card" style="left:114px">
    <div class="card-photo" role="img" aria-label="Photo of a cheerful businessman stretching under a blue sky" style="background:linear-gradient(#6ea4dc,#c9ddf0)"></div>
    <h2>Welcome To life coaching</h2>
    <p>Lorem ipsum dolor sit amet, consectetuer adipiscing elit. Praesent vestibulum molestie lacus. Aenean nonummy hendrerit mauris. Phasellus porta. Fusce cipit.Lorem ipsum dolor sit amet, consectetuer adipiscing elit. Praesent vestibulum molestie lacus.</p>
    <span class="btn">Learn More</span>
  </article>
  <article class="card" style="left:294px">
    <div class="card-photo" role="img" aria-label="Photo of a man in a suit pointing at the word coach" style="background:linear-gradient(#9cc0c2,#dde8e8)"></div>
    <h2>Life Coaching for Personal</h2>
    <p>Lorem ipsum dolor sit amet, consectetuer adipiscing elit. Praesent vestibulum molestie lacus. Aenean nonummy hendrerit mauris. Phasellus porta. Fusce cipit.Lorem ipsum dolor sit amet, consectetuer adipiscing elit. Praesent vestibulum molestie lacus.</p>
    <span class="btn">Learn More</span>
  </article>
  <article class="card" style="left:474px">
    <div class="card-photo" role="img" aria-label="Photo of a smiling businesswoman in front of a city skyline" style="background:linear-gradient(#c4d3df,#a9bccb)"></div>
    <h2>Professional Empowerment</h2>
    <p>Lorem ipsum dolor sit amet, consectetuer adipiscing elit. Praesent vestibulum molestie lacus. Aenean nonummy hendrerit mauris. Phasellus porta. Fusce cipit.Lorem ipsum dolor sit amet, consectetuer adipiscing elit. Praesent vestibulum molestie lacus.</p>
    <span class="btn">Learn More</span>
  </article>

  <h2 class="abs news-title">News &amp; <span>Events</span></h2>
  <div class="abs news-rule"></div>

  <article class="news" style="left:114px">
    <div class="news-photo" role="img" aria-label="Photo of a young man pointing forward with colleagues behind" style="background:linear-gradient(#dfe6ee,#bccbdb)"></div>
    <div class="news-body">
      <h4>Dolor nunc vule putateulr</h4>
      <div class="news-date">March-22-2011</div>
      <p>Lorem ipsum dolor sit amet, consectetuer adipiscing elit, sed diam nonummy nibh euismod tincidunt ut laoreet dolore magna aliquam erat volutpat.</p>
      <div class="news-more">Read More</div>
    </div>
  </article>
  <article class="news" style="left:382px">
    <div class="news-photo" role="img" aria-label="Photo of a businessman working on a laptop" style="background:linear-gradient(#e4e4e4,#a8a8a8)"></div>
    <div class="news-body">
      <h4>Dolor nunc vule putateulr</h4>
      <div class="news-date">March-22-2011</div>
      <p>Lorem ipsum dolor sit amet, consectetuer adipiscing elit, sed diam nonummy nibh euismod tincidunt ut laoreet dolore magna aliquam erat volutpat.</p>
      <div class="news-more">Read More</div>
    </div>
  </article>

  <section class="abs subscribe">
    <svg class="abs" style="left:115px;top:19px" width="18" height="13" viewBox="0 0 18 13"><rect x=".75" y=".75" width="16.5" height="11.5" fill="none" stroke="#fff" stroke-width="1.5"/><path d="M1 1l8 7 8-7M1 12l6-5M17 12l-6-5" fill="none" stroke="#fff" stroke-width="1.3"/></svg>
    <span class="subscribe-label">SUBSCRIBE TO OUR NEWSLETTER</span>
    <div class="subscribe-input">Enter Email</div>
    <div class="subscribe-btn">Submit</div>
  </section>

  <footer class="abs footer">
    <div class="footer-links">Home &nbsp;|&nbsp; Life Coaching &nbsp;|&nbsp; About Us &nbsp;|&nbsp; Contact Us</div>
    <div class="footer-copy">©2014 life coaching, All Rights Reserved.</div>
    <div class="social"><span></span><span></span><span></span><span></span></div>
  </footer>
</div>
</body>
</html>
```